Automotive component supplier needs a business card design

We need a business card design for our company called Velran Global Components Ltd based in the UK. We are a supplier of interior and exterior components to premium car manufacturers such as Corvel Ashby, Hadley Fenn, Marquist and Tavarelli. We would like to see a modern business card design that uses the colour blue.

Target Market(s)

Premium automotive car manufacturers.

Industry/Entity Type

Automotive

Contact Information for Business Card

Company Name : Velran Global Components Limited
Address: 17 Marlow Yard, Upper Heath, Warwick, CV31 8QL, United Kingdom
Web Address : www.velrancomponents-example.co.uk

Font styles to use
Other font styles liked:
• Helvetica

Colors
3176b5
0255a3
85acd3
cfdeed
cee9f5
85cae6
34a6d7
0692cd
9bcb3c

Requirements
Must have
• Clear company logo and a mixture of blue colours.
Nice to have
• A high quality modern image.
Should not have
• Multiple colours.

```html
<!DOCTYPE html>
<html lang="en">
<head>
<meta charset="utf-8">
<title>Velran Global Components – Business Card</title>
<link rel="stylesheet" href="https://fonts.googleapis.com/css2?family=Exo+2:wght@400;600;700&family=Open+Sans:wght@400&display=swap">
<style>
  :root {
    --backdrop: #262626;
    --card-white: #ffffff;
    --brand-blue: #0692cd;
    --accent-green: #9bcb3c;
    --text-grey: #4a4a4a;
    --white: #ffffff;
  }
  * { box-sizing: border-box; margin: 0; padding: 0; }
  html, body {
    width: 1200px; height: 987px; overflow: hidden;
    background: var(--backdrop);
    font-family: "Exo 2", Helvetica, Arial, sans-serif;
  }
  .card {
    position: absolute;
    left: 293px;
    width: 615px;
    height: 352px;
  }
  .card--front { top: 130px; background: var(--card-white); }
  .card--back { top: 505px; background: var(--brand-blue); }

  /* Brand name block */
  .brand { position: absolute; display: flex; align-items: flex-start; gap: 8px; }
  .brand__name { font-weight: 600; line-height: 1; text-transform: uppercase; }
  .brand__main { display: block; letter-spacing: 1px; }
  .brand__sub { display: block; letter-spacing: 0.5px; }
  .brand__square { background: var(--accent-green); border-radius: 2px; flex: none; }

  .card--front .brand { left: 34px; top: 44px; }
  .card--front .brand__name { color: var(--brand-blue); }
  .card--front .brand__main { font-size: 50px; }
  .card--front .brand__sub { font-size: 15px; margin-top: 4px; }
  .card--front .brand__square { width: 14px; height: 14px; margin-top: 4px; }

  .address {
    position: absolute; left: 34px; top: 156px;
    font-style: normal; font-size: 16px; line-height: 22px; color: var(--text-grey);
  }
  .contacts {
    position: absolute; left: 34px; top: 234px; list-style: none;
    font-size: 16px; color: var(--text-grey);
  }
  .contacts li { display: flex; align-items: center; gap: 8px; height: 24px; }
  .contacts li.contacts__email { font-size: 14.5px; }
  .contacts svg { width: 14px; height: 16px; flex: none; fill: var(--brand-blue); }

  .person { position: absolute; right: 33px; top: 206px; text-align: right; }
  .person__name { font-size: 21px; font-weight: 700; color: var(--brand-blue); letter-spacing: 0.3px; }
  .person__role { font-size: 16px; color: var(--accent-green); margin-top: 2px; }

  .web-band {
    position: absolute; left: 0; top: 326px; width: 571px; height: 26px;
    background: var(--brand-blue); color: var(--white);
    font-size: 15px; line-height: 26px; padding-left: 34px;
  }
  .web-tab {
    position: absolute; left: 575px; top: 326px; width: 35px; height: 26px;
    background: var(--accent-green); border-radius: 4px 4px 0 0;
  }

  /* Back */
  .card--back .brand { left: 50%; top: 128px; transform: translateX(-50%); }
  .card--back .brand__name { color: var(--white); text-align: center; }
  .card--back .brand__main { font-size: 62px; }
  .card--back .brand__sub { font-size: 18px; margin-top: 6px; }
  .card--back .brand__square { width: 16px; height: 16px; margin-top: 6px; background: var(--white); }
  .back-web {
    position: absolute; left: 0; right: 0; top: 288px; text-align: center;
    font-family: "Open Sans", Helvetica, Arial, sans-serif;
    font-size: 15px; letter-spacing: 3.5px; color: var(--white);
  }
</style>
</head>
<body>
  <section class="card card--front" aria-label="Business card front">
    <div class="brand">
      <span class="brand__name">
        <span class="brand__main">Velran</span>
        <span class="brand__sub">Global Components</span>
      </span>
      <span class="brand__square"></span>
    </div>

    <address class="address">
      17 Marlow Yard, Upper Heath<br>
      Warwick, CV31 8QL<br>
      United Kingdom
    </address>

    <ul class="contacts">
      <li>
        <svg viewBox="0 0 16 16" aria-hidden="true"><path d="M3.6 1.2l2.3 2.6c.4.4.3 1-.1 1.4L4.7 6.3c.9 2 2.6 3.8 4.7 4.8l1.1-1.1c.4-.4 1-.5 1.4-.1l2.6 2.2c.4.4.5 1 .1 1.4l-1.3 1.4C11.8 16.4 1 7.5.9 3c0-.6.3-1 .7-1.4L3 .9c.2 0 .4 0 .6.3z"/></svg>
        701 552 4186
      </li>
      <li>
        <svg viewBox="0 0 16 16" aria-hidden="true"><path d="M4.5 0h7A1.5 1.5 0 0 1 13 1.5v13a1.5 1.5 0 0 1-1.5 1.5h-7A1.5 1.5 0 0 1 3 14.5v-13A1.5 1.5 0 0 1 4.5 0zm.3 2v10.5h6.4V2zm3.2 11.3a.9.9 0 1 0 0 1.8.9.9 0 0 0 0-1.8z"/></svg>
        744 219 6053
      </li>
      <li class="contacts__email">
        <svg viewBox="0 0 16 16" aria-hidden="true"><path d="M1 4h14v9H1zm1.3 1L8 9l5.7-4z"/></svg>
        daniel@velrancomponents-example.co.uk
      </li>
    </ul>

    <div class="person">
      <p class="person__name">DANIEL HARTLEY</p>
      <p class="person__role">CEO/Founder</p>
    </div>

    <div class="web-band">www.velrancomponents-example.co.uk</div>
    <div class="web-tab"></div>
  </section>

  <section class="card card--back" aria-label="Business card back">
    <div class="brand">
      <span class="brand__name">
        <span class="brand__main">Velran</span>
        <span class="brand__sub">Global Components</span>
      </span>
      <span class="brand__square"></span>
    </div>
    <p class="back-web">www.velrancomponents-example.co.uk</p>
  </section>
</body>
</html>
```